Upmarket Dessert Lounge needs a Business Card Design

We are an upmarket dessert lounge needing a business card to match our image.

We want something that is simple yet beautiful, feminine, classy, sophisticated and elegant. We want it to stand out and don't mind if it is bold.

The design should include our logo and colours of red or maroon with gold highlights. We don't mind if black is used.

Marlow & Quince

Target Market(s)

For those who like to indulge or treat themselves and give in to their temptations on good quality desserts.

Industry/Entity Type

Business

Requirements
Must have
• Must include our logo and our name

Marlow & Quince

M & Q

```html
<!DOCTYPE html>
<html lang="en">
<head>
<meta charset="utf-8">
<title>Marlow &amp; Quince — Business Card</title>
<link rel="stylesheet" href="https://fonts.googleapis.com/css2?family=Tinos:wght@400;700&display=swap">
<style>
  :root {
    --maroon: #7a1518;
    --gold-line: #f6d9a8;
    --ink: #3a3a3a;
    --divider: #c9c9c9;
    --card: #ffffff;
    --backdrop: #ecebe8;
  }
  * { box-sizing: border-box; margin: 0; padding: 0; }
  html, body {
    width: 1200px; height: 417px; overflow: hidden;
    background: var(--backdrop);
    font-family: "Tinos", "Times New Roman", serif;
  }
  .canvas { position: relative; width: 1200px; height: 417px; }
  .card {
    position: absolute; top: 61px; width: 514px; height: 295px;
    background: var(--card);
    box-shadow: 0 2px 6px rgba(0,0,0,0.18);
  }
  .card--front { left: 54px; }
  .card--back { left: 629px; }

  .brand-name {
    position: absolute; left: 0; right: 0;
    text-align: center;
    color: var(--maroon);
    font-weight: 400;
    font-size: 64px;
    line-height: 1;
    letter-spacing: 2px;
  }
  .card--front .brand-name { top: 70px; }
  .card--back .brand-name { top: 95px; }

  .person {
    position: absolute; top: 203px; left: 0; right: 0;
    text-align: center; color: var(--maroon);
  }
  .person__name { font-weight: 700; font-size: 17px; letter-spacing: 0.3px; }
  .person__title { font-size: 13px; color: var(--ink); }

  .rule {
    position: absolute; top: 233px; left: 34px; width: 456px; height: 3px;
    background: var(--gold-line);
  }

  .contacts {
    position: absolute; top: 247px; left: 36px; right: 20px;
    display: flex; font-size: 13px; color: var(--ink); line-height: 19px;
  }
  .contacts__col { padding-right: 14px; }
  .contacts__col--address { width: 130px; }
  .contacts__col--phone { width: 150px; border-left: 1px solid var(--divider); padding-left: 10px; }
  .contacts__col--web { border-left: 1px solid var(--divider); padding-left: 10px; }
  .contact-line { display: flex; align-items: center; gap: 6px; white-space: nowrap; }
  .icon { width: 10px; height: 10px; fill: var(--maroon); flex: none; }

  .web-address {
    position: absolute; top: 242px; left: 0; right: 0;
    text-align: center; font-size: 13px; letter-spacing: 2.2px; color: #222;
  }
</style>
</head>
<body>
<main class="canvas">
  <section class="card card--front">
    <div class="brand-name">M &amp; Q</div>
    <div class="person">
      <span class="person__name">YOUR NAME /</span>
      <span class="person__title">Title</span>
    </div>
    <div class="rule"></div>
    <div class="contacts">
      <div class="contacts__col contacts__col--address">
        <div>00, Complex name</div>
        <div>City, State 000 000</div>
      </div>
      <div class="contacts__col contacts__col--phone">
        <div class="contact-line">
          <svg class="icon" viewBox="0 0 10 10" aria-hidden="true"><circle cx="5" cy="5" r="5"/><path d="M3 2.5c0 2.5 2 4.5 4.5 4.5l.5-1-1.3-.7-.6.6c-.9-.4-1.6-1.1-2-2l.6-.6L4 2z" fill="#fff"/></svg>
          <span>+2348005550142</span>
        </div>
        <div class="contact-line">
          <svg class="icon" viewBox="0 0 10 10" aria-hidden="true"><rect x="2" y="0" width="6" height="10" rx="1"/><rect x="3" y="1.5" width="4" height="5" fill="#fff"/></svg>
          <span>+2348005550142</span>
        </div>
      </div>
      <div class="contacts__col contacts__col--web">
        <div class="contact-line">
          <svg class="icon" viewBox="0 0 10 10" aria-hidden="true"><rect x="0" y="2" width="10" height="6.5"/><path d="M0.5 2.5 5 5.8 9.5 2.5" stroke="#fff" stroke-width="0.9" fill="none"/></svg>
          <span>hello@marlowquince.com</span>
        </div>
        <div class="contact-line">
          <svg class="icon" viewBox="0 0 10 10" aria-hidden="true"><circle cx="5" cy="5" r="5"/><path d="M0.5 5h9M5 0.5c-2 2.5-2 6.5 0 9M5 0.5c2 2.5 2 6.5 0 9" stroke="#fff" stroke-width="0.8" fill="none"/></svg>
          <span>www.marlowquince.com</span>
        </div>
      </div>
    </div>
  </section>

  <section class="card card--back">
    <div class="brand-name">M &amp; Q</div>
    <div class="web-address">www.marlowquince.com</div>
  </section>
</main>
</body>
</html>
```